New Business Card Design for Manufacturing

We are an engineering/manufacturing company that offers Advanced machining/assembly/engineering services, as well as innovative products for the heavy duty engine cooling markets.

We are looking to get a new business card designed that is clean and modern looking, but still fits the wide range of technical/skilled work we do.

- We hope to use this design as the base for other design work in new Presentations, web, and print work.

Industry/Entity Type

Engineering

Contact Information for Business Card

Our preferred color of blue is (RGB) 22/71/159 but can vary slightly from that color. Our content will be our Logo and full company name (Vantrell Forge Works, Inc.), company address, name, job title, phone number with extension, cell number, fax number, website, and email address on the cards.
We'd like the full company name next to the logo, but we are open to other interpretations of that layout.
Preferably, we would like the back side to be clean with just our logo, and the front to contain all of the contact information.

Colors
2f74b4
0355a3
85abd2

Requirements
Must have
• - Logo, company name, needed content - We are open to interpretation beyond that.
• - Standard size business card.
• - Horizontal orientation.
• - Enough space for lengthy names / job titles (for example, a job title could read "Directory of Human Resources" or "V.P. of Governmental Affairs"). We need this to look clean, whether the title be short (CEO) or long (as described above).

```html
<!DOCTYPE html>
<html lang="en">
<head>
<meta charset="utf-8">
<title>Vantrell Forge Works — Business Card</title>
<link rel="stylesheet" href="https://fonts.googleapis.com/css2?family=Archivo:wght@800&family=Open+Sans:wght@400;600&display=swap">
<style>
  :root {
    --brand-blue: #16479f;
    --ink: #3a3c40;
    --paper: #f4f3f0;
    --backdrop: #d3d8d9;
    --rule: #6b6e73;
  }
  * { box-sizing: border-box; margin: 0; padding: 0; }
  html, body { width: 1200px; height: 897px; overflow: hidden; }
  body {
    background: var(--backdrop);
    display: flex;
    align-items: center;
    justify-content: center;
    gap: 48px;
    font-family: "Open Sans", sans-serif;
  }
  .card {
    width: 525px;
    height: 300px;
    position: relative;
    box-shadow: 0 2px 6px rgba(0,0,0,0.12);
  }
  .card--front { background: var(--paper); color: var(--ink); }
  .card--back {
    background: var(--brand-blue);
    display: flex;
    align-items: center;
    justify-content: center;
  }
  .wordmark {
    display: flex;
    align-items: center;
    gap: 10px;
    font-family: "Archivo", sans-serif;
    font-weight: 800;
    text-transform: uppercase;
    line-height: 1.05;
    letter-spacing: 0.02em;
  }
  .wordmark__mark { flex: none; }
  .card--front .wordmark {
    position: absolute;
    top: 36px;
    right: 34px;
    color: var(--brand-blue);
    font-size: 15px;
  }
  .card--front .wordmark__mark { width: 34px; height: 34px; background: var(--brand-blue); }
  .card--back .wordmark { color: #fff; font-size: 26px; gap: 16px; }
  .card--back .wordmark__mark { width: 58px; height: 58px; border: 4px solid #fff; }
  .contact {
    position: absolute;
    left: 34px;
    top: 104px;
    right: 34px;
  }
  .contact__name {
    font-weight: 600;
    font-size: 20px;
    letter-spacing: 0.06em;
    color: var(--brand-blue);
    text-transform: uppercase;
  }
  .contact__title { font-size: 13px; margin-top: 2px; }
  .contact__rule { width: 46px; height: 1px; background: var(--rule); margin: 10px 0 12px; }
  .contact__line { font-size: 12.5px; line-height: 1.5; }
  .contact__line--accent { color: var(--brand-blue); }
  .contact__line a { color: var(--brand-blue); text-decoration: none; }
</style>
</head>
<body>
  <section class="card card--front" aria-label="Business card front">
    <div class="wordmark">
      <span class="wordmark__mark"></span>
      <span>Vantrell<br>Forge<br>Works, Inc.</span>
    </div>
    <div class="contact">
      <h1 class="contact__name">Dorian Hale</h1>
      <p class="contact__title">Directory of Human Resources</p>
      <div class="contact__rule"></div>
      <p class="contact__line">P: 2210 ext | C: 555-014-2290 | F: (555)014-2291</p>
      <p class="contact__line">E: dhale@vantrellforge.com | <a href="#">www.vantrellforge.com</a></p>
      <p class="contact__line contact__line--accent">Vantrell Forge Works, Inc.</p>
      <p class="contact__line">480 Kessler Ave. Dunmore Bay, FL 33190</p>
    </div>
  </section>
  <section class="card card--back" aria-label="Business card back">
    <div class="wordmark">
      <span class="wordmark__mark"></span>
      <span>Vantrell<br>Forge<br>Works, Inc.</span>
    </div>
  </section>
</body>
</html>
```